Dental Practice Website design

Design a new website for Brambleford Dental Practice.
Design should be warm, neutral in colour, with some small amount of bright colour if needed but kept to a minimum. Website should look professional, high end. Home page should be easy to navigate and simple for patients to be able to book online.
Logo in files along with some examples of websites that we like. Please ask if any further info needed.
Menu should have:
About
New Patients
Treatments
Fees
Contact Us

Industry/Entity Type

Dentistry

Number of Pages Required

4 page

Font styles to use
Sans Serif

Colors

Designer to choose colors to be used in the design.

Requirements
Must have
• Ravelle ratings badge, book online button,
Nice to have
• neutral, relaxing colours
Should not have
• harsh, bright colours!

```html
<!DOCTYPE html>
<html lang="en">
<head>
<meta charset="utf-8">
<title>Brambleford Dental Practice – Home</title>
<link href="https://fonts.googleapis.com/css2?family=Figtree:wght@300;400;500;600&display=swap" rel="stylesheet">
<style>
:root{
  --page:#ffffff;
  --sand:#f3f1ed;
  --mist:#e8ebee;
  --blue:#56779a;
  --blue-soft:#dfe6ee;
  --navy:#27334a;
  --ink:#1f2533;
  --muted:#6e717a;
  --black:#15161a;
  --gold:#c9a46a;
}
*{box-sizing:border-box;margin:0;padding:0}
html,body{width:1200px;height:1200px;overflow:hidden;background:var(--page);font-family:'Figtree',sans-serif;color:var(--ink)}
.col{position:absolute;top:0;width:482px;height:1200px;background:var(--sand);overflow:hidden}
.col-left{left:83px}
.col-right{left:633px}
.abs{position:absolute}
.photo{position:absolute}
h2,h1{font-weight:300;line-height:1.05;letter-spacing:-.01em}
h1 b,h2 b{font-weight:600}
.eyebrow{position:absolute;font-size:4px;display:flex;align-items:center;gap:5px;color:var(--ink)}
.eyebrow svg{width:10px;height:10px}
.small{font-size:3.4px;line-height:1.75;color:var(--muted)}
.link{font-size:4.2px;text-decoration:underline;color:var(--ink)}
.btn{position:absolute;font-size:4px;border-radius:8px;padding:3px 8px;white-space:nowrap}
.btn-solid{background:var(--blue);color:#fff}
.btn-ghost{border:.6px solid currentColor}
/* hero */
.hero{position:absolute;left:0;top:0;width:482px;height:250px;background:linear-gradient(100deg,#eef0f3 0%,#dde2e8 40%,#c4c3c6 65%,#c9a08a 100%)}
.nav{position:absolute;top:12px;left:38px;right:38px;display:flex;align-items:center;font-size:3.6px;color:#fff}
.brand{font-size:5px;font-weight:400;line-height:1;color:#fff;display:flex;align-items:center;gap:3px}
.brand i{width:6px;height:6px;border:.6px solid #fff;display:block}
.menu{display:flex;gap:5px;margin-left:55px}
.phone{margin-left:auto;margin-right:8px}
.hero h1{position:absolute;left:38px;top:113px;font-size:30px;color:var(--ink)}
.pills{position:absolute;left:38px;top:196px;display:flex;gap:2.5px}
.pills span{font-size:3.2px;border:.5px solid var(--ink);border-radius:6px;padding:1.5px 5px}
.rating{position:absolute;left:400px;top:200px;width:44px;height:26px;border-radius:4px;background:rgba(255,255,255,.85);box-shadow:0 2px 6px rgba(0,0,0,.08);display:flex;flex-direction:column;align-items:center;justify-content:center;gap:3px}
.rating .mark{width:8px;height:8px;border-radius:50%;background:var(--gold)}
/* cards */
.svc{position:absolute;top:706px;width:113px;height:119px}
.svc-label{position:absolute;top:830px;font-size:8.5px;line-height:1.3;font-weight:400}
.svc-label small{font-size:4px;margin-right:2px}
/* pricing */
.plan{position:absolute;top:351px;width:131px;height:163px;background:#fff;padding:18px 12px}
.plan.featured{background:var(--blue);color:#fff;box-shadow:0 6px 14px rgba(0,0,0,.1)}
.plan .price{font-size:12px;font-weight:400}
.plan .price small{font-size:4px}
.plan p{font-size:3.3px;line-height:1.6;margin-top:6px;opacity:.8}
.plan ul{list-style:none;margin-top:8px}
.plan li{font-size:3.3px;display:flex;align-items:center;gap:4px;height:12.6px;opacity:.85}
.plan li::before{content:"";width:5px;height:5px;border:.5px solid currentColor;border-radius:50%}
.plan .btn{position:static;display:inline-block;margin-top:6px}
.plan.featured .btn{background:#fff;color:var(--blue)}
/* team */
.member{position:absolute;top:684px;width:96px;height:106px}
.member-bar{position:absolute;top:775px;width:87px;height:20px;background:#fff;padding:4px 5px;font-size:7px;display:flex;justify-content:space-between}
.member-bar small{display:block;font-size:3px;color:var(--muted)}
.dots{display:flex;gap:1.5px;margin-top:2px}
.dots i{width:4.5px;height:4.5px;border-radius:50%;background:var(--blue)}
/* contact */
.field{position:absolute;left:11px;border:.5px solid #d5d8dd;font-size:3.2px;color:var(--muted);padding:6px 7px}
.info{position:absolute;left:38px;display:flex;gap:5px;font-size:4.4px}
.info small{display:block;font-size:3.3px;color:var(--muted)}
.icon{width:14px;height:14px;border-radius:50%;background:var(--blue);display:flex;align-items:center;justify-content:center}
.icon svg{width:7px;height:7px}
/* footer */
.footer{position:absolute;left:0;top:1054px;width:482px;height:146px;background:var(--black);color:#fff}
.fcol{position:absolute;top:36px}
.fcol h4{font-weight:300;font-size:9px;margin-bottom:6px}
.fcol p{font-size:3.3px;line-height:2.6}
</style>
</head>
<body>
<svg width="0" height="0" style="position:absolute">
  <symbol id="spark" viewBox="0 0 20 20"><path d="M10 0v20M0 10h20M3 3l14 14M17 3L3 17" stroke="currentColor" stroke-width="1"/></symbol>
  <symbol id="star" viewBox="0 0 10 10"><path d="M5 .5l1.3 2.9 3.2.3-2.4 2.1.7 3.1L5 7.3 2.2 8.9l.7-3.1L.5 3.7l3.2-.3z" fill="currentColor"/></symbol>
</svg>

<!-- LEFT COLUMN -->
<div class="col col-left">
  <section class="hero" role="img" aria-label="Dentist examining a smiling patient in a bright clinic">
    <nav class="nav">
      <div class="brand"><i></i>BRAMBLEFORD</div>
      <div class="menu"><span>Home</span><span>About us</span><span>Treatments</span><span>New Patients</span><span>Fees</span><span>Contact Us</span></div>
      <span class="phone">+(44)100-2040</span>
      <span class="btn btn-solid" style="position:static">Book Appointment</span>
    </nav>
    <div class="eyebrow" style="left:38px;top:99px;color:var(--blue)"><svg><use href="#spark"/></svg>Expert care with a personal touch</div>
    <h1>Bright Smiles,<br>Gentle <b>Care</b></h1>
    <div class="pills"><span>Services</span><span>Treatments</span><span>Equipments</span><span>Painless</span><span>Doctors</span></div>
    <p class="small abs" style="left:38px;top:210px;width:140px;color:#4b5566">Welcome to our friendly dental practice nestled in the heart of beautiful Thornbury Vale, UK. Our team of dedicated dentists, hygienists and support staff are here to provide you with exceptional dental care.</p>
    <div class="rating" role="img" aria-label="Ravelle ratings badge, five stars">
      <span class="mark"></span>
      <svg width="30" height="5" viewBox="0 0 30 5" style="color:var(--gold)"><use href="#star" width="5" height="5"/><use href="#star" x="6" width="5" height="5"/><use href="#star" x="12" width="5" height="5"/><use href="#star" x="18" width="5" height="5"/><use href="#star" x="24" width="5" height="5"/></svg>
    </div>
  </section>

  <h2 class="abs" style="left:141px;top:302px;font-size:17.5px">Where Expertise Meets<br><b>Compassion</b></h2>
  <div class="abs" style="left:0;top:417px;width:38px;height:154px;background:var(--mist)"></div>
  <div class="photo" style="left:38px;top:359px;width:187px;height:173px;background:linear-gradient(135deg,#c9b9a8,#e9dfd4 50%,#bcc9d6)" role="img" aria-label="Smiling patient during a check-up"></div>
  <div class="photo" style="left:134px;top:444px;width:104px;height:127px;background:linear-gradient(160deg,#e8ebed,#c3ced9 60%,#93a8be)" role="img" aria-label="Dentist treating a patient in the chair"></div>
  <div class="abs" style="left:279px;top:383px;width:140px">
    <p style="font-size:4px;line-height:1.7;font-weight:500">Our dedicated team is committed to making your dental experience comfortable, pain-free, and rewarding</p>
    <p class="small" style="margin-top:5px">At our practice, we believe that a visit to the dentist should be a comfortable and positive experience. We strive to create a warm and welcoming atmosphere where our patients can feel at ease and confident in the care they receive. Our modern facilities and equipment mean that you can trust us to deliver the latest techniques and treatments to ensure your oral health is at its best.</p>
    <p class="small" style="margin-top:4px">We are passionate about improving dental health and helping you achieve your brightest smile, and are honoured that you're considering us for your dental needs. Please don't hesitate to contact us if you have any questions or to schedule an appointment. We look forward to welcoming you to our practice.</p>
    <p class="link" style="margin-top:6px">Get to Know Us</p>
  </div>

  <div class="abs" style="left:0;top:571px;width:482px;height:230px;background:var(--mist)"></div>
  <div class="eyebrow" style="left:38px;top:605px"><svg><use href="#spark"/></svg>Explore Our Services</div>
  <h2 class="abs" style="left:38px;top:621px;font-size:17.5px">Comprehensive Care<br>for Every <b>Smile</b></h2>
  <div class="abs" style="left:307px;top:627px;width:140px">
    <p class="small">If you're looking for an exceptional dental practice, we're here to help! Our team is made up of highly skilled professionals who are dedicated to ensuring that all our patients receive top-notch care in a welcoming and comfortable environment.</p>
    <p class="link" style="margin-top:5px">View All Treatments</p>
  </div>
  <div class="svc" style="left:38px;background:linear-gradient(160deg,#eef0f2,#c8d2dc 60%,#93a8be)" role="img" aria-label="General dentistry check-up"></div>
  <div class="svc" style="left:157px;background:linear-gradient(180deg,#f0d8d2,#f5f0ea 55%,#e4dcd0)" role="img" aria-label="Tooth shade guide for cosmetic work"></div>
  <div class="svc" style="left:276px;background:linear-gradient(160deg,#e3e8ee,#f4efe9 50%,#d9b7a5)" role="img" aria-label="Orthodontic examination"></div>
  <div class="svc" style="left:396px;width:86px;background:linear-gradient(180deg,#d8e0e8,#9fb3c7 70%,#7890aa)" role="img" aria-label="Emergency dental treatment"></div>
  <p class="svc-label" style="left:38px"><small>.01</small>General Dentistry</p>
  <p class="svc-label" style="left:157px"><small>.02</small>Cosmetic Dentistry</p>
  <p class="svc-label" style="left:276px"><small>.03</small>Orthodontics</p>
  <p class="svc-label" style="left:396px"><small>.04</small>Emergency Dental<br><span style="margin-left:10px">Care</span></p>
  <span class="abs" style="left:38px;top:875px;font-size:4px">01/06</span>
  <div class="abs" style="left:55px;top:877.5px;width:276px;height:.5px;background:var(--ink)"></div>
  <svg class="abs" style="left:376px;top:870px" width="40" height="15" viewBox="0 0 40 15">
    <circle cx="7.5" cy="7.5" r="7.5" fill="#fff"/><circle cx="27.5" cy="7.5" r="7.5" fill="#fff"/>
    <path d="M11 7.5H4M6.5 5L4 7.5 6.5 10M24 7.5h7M28.5 5L31 7.5 28.5 10" stroke="#1f2533" stroke-width=".7" fill="none"/>
  </svg>

  <div class="photo" style="left:0;top:935px;width:307px;height:187px;background:linear-gradient(120deg,#b28f78,#e6d5c8 45%,#d6dde5 70%,#a7b9cb)" role="img" aria-label="Smiling man having a dental check-up"></div>
  <div class="abs" style="left:245px;top:998px;width:237px;height:161px;background:var(--blue);color:#fff;padding:22px 28px">
    <div class="eyebrow" style="position:static;color:#fff"><svg><use href="#spark"/></svg>Your First Visit?</div>
    <h2 style="font-size:17.5px;margin-top:6px">Let's Make It<br><b>Effortless</b></h2>
    <p class="small" style="color:#e1e7ee;margin-top:7px">Our practice is always up-to-date with the latest techniques and technologies to make sure that our patients receive the best possible results.</p>
    <p class="small" style="color:#e1e7ee;margin-top:4px">We understand that dental care can be expensive which is why we offer affordable prices to ensure that everyone has access to quality care. If you'd like to learn more about our practice, please don't hesitate to contact us.</p>
    <span class="btn btn-ghost" style="position:static;display:inline-block;margin-top:8px">Book Your First Appointment</span>
  </div>
</div>

<!-- RIGHT COLUMN -->
<div class="col col-right">
  <h2 class="abs" style="left:38px;top:-6px;font-size:17.5px">Dental <b>Practice?</b></h2>
  <p class="small abs" style="left:313px;top:0;width:130px">dental care possible.</p>
  <div class="abs" style="left:0;top:29px;width:134px;height:211px;background:var(--navy)"></div>
  <div class="photo" style="left:38px;top:29px;width:172px;height:178px;background:linear-gradient(150deg,#f2e4da,#d8b29b 55%,#c89a82)" role="img" aria-label="Close-up of a smile while flossing"></div>
  <div class="abs" style="left:244px;top:54px;width:210px;display:grid;grid-template-columns:104px 104px;row-gap:14px">
    <div><svg width="12" height="12" viewBox="0 0 12 12"><circle cx="6" cy="4" r="2.5" fill="none" stroke="#56779a" stroke-width=".6"/><path d="M1.5 11.5c0-3 2-4.5 4.5-4.5s4.5 1.5 4.5 4.5" fill="none" stroke="#56779a" stroke-width=".6"/></svg><p style="font-size:6px;line-height:1.1;margin-top:2px">Gentle And<br>Experienced Team</p><p class="small" style="margin-top:4px">We prioritize your comfort and care.</p></div>
    <div><svg width="12" height="12" viewBox="0 0 12 12"><rect x="1" y="1" width="10" height="7" rx="1" fill="none" stroke="#56779a" stroke-width=".6"/><path d="M4 11h4M6 8v3" stroke="#56779a" stroke-width=".6"/></svg><p style="font-size:6px;line-height:1.1;margin-top:2px">State of the Art<br>Technology</p><p class="small" style="margin-top:4px">Modern treatments for precise results.</p></div>
    <div><svg width="12" height="12" viewBox="0 0 12 12"><circle cx="6" cy="6" r="4.5" fill="none" stroke="#56779a" stroke-width=".6"/><path d="M6 3.5v5M4.5 5h2.5M4.5 7h3" stroke="#56779a" stroke-width=".6"/></svg><p style="font-size:6px;line-height:1.1;margin-top:2px">Affordable<br>Transparent Pricing</p><p class="small" style="margin-top:4px">No hidden costs, just great care.</p></div>
    <div><svg width="12" height="12" viewBox="0 0 12 12"><rect x="2.5" y="1" width="7" height="10" rx="1" fill="none" stroke="#56779a" stroke-width=".6"/><path d="M4.5 4h3M4.5 6h3" stroke="#56779a" stroke-width=".6"/></svg><p style="font-size:6px;line-height:1.1;margin-top:2px">A Family Friendly<br>Environment</p><p class="small" style="margin-top:4px">Welcoming patients of all ages!</p></div>
  </div>
  <p class="abs" style="left:244px;top:168px;font-size:3.4px;color:var(--muted)">Ready for a Healthier, Brighter Smile? <span class="link" style="margin-left:4px">Contact us today</span></p>

  <div class="eyebrow" style="left:221px;top:282px"><svg><use href="#spark"/></svg>Our Pricing</div>
  <h2 class="abs" style="left:0;width:482px;top:297px;text-align:center;font-size:17.5px">Transparent Pricing for<br>Quality Dental <b>Care</b></h2>
  <div class="plan featured" style="left:38px"><p class="price">$19.99/<small>Basic Plan</small></p><p>Varius egestas amet eleifend risus consectetur. Diam porta ornare id diam</p><ul><li>Varius egestas amet eleifend risus.</li><li>Varius egestas amet eleifend risus.</li><li>Varius egestas amet eleifend risus.</li><li>Varius egestas amet eleifend risus.</li><li>Varius egestas amet eleifend risus.</li><li>Varius egestas amet eleifend risus.</li></ul><span class="btn">Book Appointment</span></div>
  <div class="plan" style="left:175px"><p class="price">$39.99/<small>Gold Plan</small></p><p>Varius egestas amet eleifend risus consectetur. Diam porta ornare id diam</p><ul><li>Varius egestas amet eleifend risus.</li><li>Varius egestas amet eleifend risus.</li><li>Varius egestas amet eleifend risus.</li><li>Varius egestas amet eleifend risus.</li><li>Varius egestas amet eleifend risus.</li><li>Varius egestas amet eleifend risus.</li></ul><span class="btn btn-solid">Book Appointment</span></div>
  <div class="plan" style="left:313px"><p class="price">$59.99/<small>Gold Plan</small></p><p>Varius egestas amet eleifend risus consectetur. Diam porta ornare id diam</p><ul><li>Varius egestas amet eleifend risus.</li><li>Varius egestas amet eleifend risus.</li><li>Varius egestas amet eleifend risus.</li><li>Varius egestas amet eleifend risus.</li><li>Varius egestas amet eleifend risus.</li><li>Varius egestas amet eleifend risus.</li></ul><span class="btn btn-solid">Book Appointment</span></div>

  <div class="abs" style="left:0;top:570px;width:204px;height:186px;background:var(--navy);color:#fff;padding:20px 0 0 38px">
    <div class="eyebrow" style="position:static;color:#fff"><svg><use href="#spark"/></svg>Our Team</div>
    <h2 style="font-size:17.5px;margin-top:6px">Meet Our Expert<br>Dental <b>Team</b></h2>
    <p class="small" style="color:#c8cdd6;margin-top:7px;width:135px">We are delighted to introduce you to our experienced and compassionate dental team. Our team comprises highly skilled dental professionals who are dedicated to providing you with high-quality dental care services.</p>
    <span class="btn btn-ghost" style="position:static;display:inline-block;margin-top:8px;margin-left:-2px">View All Experts</span>
  </div>
  <div class="member" style="left:141px;background:linear-gradient(180deg,#e8ecef,#c9b4a2)" role="img" aria-label="Portrait of Owen Hartley"></div>
  <div class="member" style="left:245px;background:linear-gradient(180deg,#eceff1,#c79a82)" role="img" aria-label="Portrait of Clara Wynn"></div>
  <div class="member" style="left:348px;background:linear-gradient(180deg,#f1f1f0,#d8bba2)" role="img" aria-label="Portrait of Lena Marsh"></div>
  <div class="member-bar" style="left:146px;background:var(--blue);color:#fff"><div>Owen Hartley<small style="color:#e1e7ee">Sr. Expert Doctor</small></div><div class="dots"><i style="background:#fff"></i><i style="background:#fff"></i><i style="background:#fff"></i></div></div>
  <div class="member-bar" style="left:250px"><div>Clara Wynn<small>Sr. Expert Doctor</small></div><div class="dots"><i></i><i></i><i></i></div></div>
  <div class="member-bar" style="left:353px"><div>Lena Marsh<small>Sr. Expert Doctor</small></div><div class="dots"><i></i><i></i><i></i></div></div>

  <div class="abs" style="left:0;top:902px;width:482px;height:152px;background:var(--mist)"></div>
  <div class="eyebrow" style="left:38px;top:840px"><svg><use href="#spark"/></svg>Let's Connect</div>
  <h2 class="abs" style="left:38px;top:856px;font-size:17.5px">Your Healthiest<br>Smile Starts <b>Here</b></h2>
  <div class="info" style="top:920px"><span class="icon"><svg viewBox="0 0 10 10"><path d="M2 1l2 2-1 1.5a6 6 0 0 0 2.5 2.5L7 6l2 2-1.5 1.5C5 9.5.5 5 .5 2.5z" fill="#fff"/></svg></span><div>Call Us:<small>+(44)100-2040</small></div></div>
  <div class="info" style="top:947px"><span class="icon"><svg viewBox="0 0 10 10"><rect x="1" y="2.5" width="8" height="5.5" fill="#fff"/><path d="M1 2.5l4 3 4-3" stroke="#56779a" stroke-width=".7" fill="none"/></svg></span><div>Email Us:<small>hello@brambleford.co</small></div></div>
  <div class="info" style="top:974px"><span class="icon"><svg viewBox="0 0 10 10"><path d="M5 9.5S1.8 6 1.8 4a3.2 3.2 0 0 1 6.4 0C8.2 6 5 9.5 5 9.5z" fill="#fff"/><circle cx="5" cy="4" r="1.2" fill="#56779a"/></svg></span><div>Location:<small>12 Mill Lane, Thornbury Vale, UK</small></div></div>
  <div class="abs" style="left:273px;top:840px;width:171px;height:186px;background:#fff;box-shadow:0 4px 12px rgba(0,0,0,.08)">
    <h2 class="abs" style="left:11px;top:15px;font-size:17px;font-weight:400">Send Message</h2>
    <div class="field" style="top:41px;width:74px;height:16px">First name</div>
    <div class="field" style="top:41px;left:87px;width:74px;height:16px">Last Name</div>
    <div class="field" style="top:62px;width:150px;height:16px">Email</div>
    <div class="field" style="top:83px;width:150px;height:16px">Phone:</div>
    <div class="field" style="top:105px;width:150px;height:37px">Write a Message</div>
    <div class="abs" style="left:11px;top:147px;width:150px;height:12px;border-radius:6px;background:var(--blue);color:#fff;font-size:4px;text-align:center;line-height:12px">Book Appointment</div>
    <p class="small abs" style="left:20px;top:166px;width:132px;text-align:center">Appointments confirmed by <b style="color:var(--ink)">email within</b> one working day. Thank you for <b style="color:var(--ink)">choosing us</b></p>
  </div>

  <footer class="footer">
    <div class="abs" style="left:38px;top:24px">
      <div class="brand" style="font-size:8px"><i style="width:9px;height:9px"></i>BRAMBLEFORD</div>
      <p class="small" style="color:#bfc3ca;width:92px;margin-top:8px">Welcome to our friendly dental practice nestled in the heart of beautiful Thornbury Vale, UK. Our team of dedicated dentists, hygienists and support staff are here to provide you with exceptional dental care.</p>
      <div class="dots" style="margin-top:8px;gap:5px"><i style="width:10px;height:10px"></i><i style="width:10px;height:10px"></i><i style="width:10px;height:10px"></i><i style="width:10px;height:10px"></i></div>
    </div>
    <div class="fcol" style="left:169px"><h4>Quick Links</h4><p>Home<br>About us<br>Treatments<br>New Patients<br>Fees<br>Contact Us</p></div>
    <div class="fcol" style="left:265px"><h4>Treatments</h4><p>General Dentistry<br>Cosmetic Dentistry<br>Orthodontics<br>Emergency Dental Care</p></div>
    <div class="fcol" style="left:361px"><h4>Contact Us</h4><p>+(44)100-2040<br>hello@brambleford.co<br>12 Mill Lane, Thornbury Vale</p></div>
    <div class="abs" style="left:0;top:125px;width:482px;height:.4px;background:#333"></div>
    <p class="abs" style="left:38px;top:133px;font-size:3.4px;color:#bfc3ca">© 2025 Brambleford Dental Practice. All rights reserved.</p>
    <p class="abs" style="right:38px;top:133px;font-size:3.4px;color:#bfc3ca">Terms &amp; Conditions . faqs . Privacy Policy</p>
  </footer>
</div>
</body>
</html>
```